IT Company that provides secure IT solutions and services to our customers

We need business cards and a logo for a new IT Solutions company just created based in Kuala Lumpur, Malaysia. But will also be serving other countries in the region. We provide secure data, voice solutions on mobile platforms. Our first offering is encrypted voice and data solutions for IOS, Android, Windows and BlackBerry devices.

Target Market(s)

large organizations Govt, Police, Defence, Anti-corruption, Legal, highly regulated industries such as Health-care, Financial, Banking, Insurance,

Industry/Entity Type

Information Technology

Contact Information for Business Card

VelmoraNet (Logo - colour is ORVEX blue)Roshan Adeel Managing Director Kryption IT Sdn. Bhd.5th Floor, Block D, Wisma PLB,No.14 Jalan Seri Melor,50470, Kuala LumpurMalaysia

Font styles to use
Sans Serif

Colors
3176b5
ec1f27
fbed22

Requirements
Must have
• VelmoraNet all in Blue like ORVEX blue. A logo design perhaps a play of VN, K with a dangling T (colour can be any)
Nice to have
• I want a clean crisp card, not too busy, easy to read.

```html
<!DOCTYPE html>
<html lang="en">
<head>
<meta charset="utf-8">
<title>VelmoraNet Business Card</title>
<link rel="stylesheet" href="https://fonts.googleapis.com/css2?family=Open+Sans:wght@400;600;700&display=swap">
<style>
  :root {
    --page-bg: #e6e8eb;
    --brand-blue: #3176b5;
    --brand-blue-deep: #2a66ad;
    --brand-blue-light: #4a8fd0;
    --logo-blue: #1f8ad6;
    --paper: #ffffff;
    --ink-dark: #2e2e2e;
    --divider: #9aa3ad;
    --text-light: #ffffff;
  }
  * { box-sizing: border-box; margin: 0; padding: 0; }
  html, body {
    width: 1200px; height: 900px; overflow: hidden;
    background: var(--page-bg);
    font-family: "Open Sans", Arial, sans-serif;
  }
  .canvas { position: relative; width: 1200px; height: 900px; }

  .card {
    position: absolute; left: 250px; width: 700px; height: 400px;
    border-radius: 4px; overflow: hidden;
    box-shadow: 0 6px 18px rgba(0,0,0,0.18);
  }

  /* Front */
  .card-front {
    top: 40px;
    background: linear-gradient(135deg, var(--brand-blue-deep) 0%, var(--brand-blue) 55%, var(--brand-blue-light) 100%);
  }
  .front-brand {
    position: absolute; right: 70px; top: 70px;
    display: flex; flex-direction: column; align-items: center;
    color: var(--text-light);
  }
  .front-brand .brand-square {
    width: 130px; height: 130px; background: var(--paper);
  }
  .front-brand .brand-name {
    margin-top: 14px; font-size: 30px; font-weight: 600; letter-spacing: 0.5px;
  }
  .front-brand .brand-url { font-size: 16px; font-weight: 400; margin-top: 2px; }

  /* Back */
  .card-back { top: 470px; display: flex; }
  .back-logo-panel {
    width: 270px; background: var(--paper);
    display: flex; flex-direction: column; align-items: center; justify-content: center;
  }
  .back-logo-panel .brand-square {
    width: 150px; height: 150px; background: var(--logo-blue);
  }
  .back-logo-panel .brand-name {
    margin-top: 16px; font-size: 32px; font-weight: 600; color: var(--ink-dark);
  }
  .back-divider { width: 14px; background: var(--divider); }
  .back-info {
    flex: 1; color: var(--text-light); padding: 44px 36px 0 40px;
    background: linear-gradient(135deg, var(--brand-blue-deep) 0%, var(--brand-blue) 60%, var(--brand-blue-light) 100%);
  }
  .person-name { font-size: 20px; font-weight: 700; line-height: 1.2; }
  .person-title { font-size: 17px; font-weight: 400; margin-bottom: 20px; }
  .contact-list { list-style: none; font-size: 15px; line-height: 1.5; }
  .contact-item { display: flex; align-items: flex-start; gap: 12px; margin-bottom: 4px; }
  .contact-item.address { font-size: 13.5px; margin-bottom: 14px; }
  .contact-icon {
    flex: none; width: 20px; height: 18px; margin-top: 2px;
    background: var(--paper); border-radius: 2px;
    display: flex; align-items: center; justify-content: center;
  }
  .contact-icon svg { width: 14px; height: 14px; fill: var(--brand-blue); }
</style>
</head>
<body>
<main class="canvas">

  <section class="card card-front" aria-label="Card front">
    <div class="front-brand">
      <div class="brand-square"></div>
      <div class="brand-name">VelmoraNet</div>
      <div class="brand-url">www.velmoranet.com</div>
    </div>
  </section>

  <section class="card card-back" aria-label="Card back">
    <div class="back-logo-panel">
      <div class="brand-square"></div>
      <div class="brand-name">VelmoraNet</div>
    </div>
    <div class="back-divider"></div>
    <div class="back-info">
      <p class="person-name">Roshan Adeel</p>
      <p class="person-title">Managing Director</p>
      <ul class="contact-list">
        <li class="contact-item address">
          <span class="contact-icon"><svg viewBox="0 0 14 14"><path d="M7 1 1 6.5h2V13h3V9h2v4h3V6.5h2z"/></svg></span>
          <span>Velmora Net Sdn. Bhd. 5th Floor, Block D,<br>Wisma PLB,No.14 Jalan Seri Melor,<br>50470, Kuala LumpurMalaysia</span>
        </li>
        <li class="contact-item">
          <span class="contact-icon"><svg viewBox="0 0 14 14"><path d="M3 2h2l1 3-1.5 1a7 7 0 0 0 3.5 3.5L9 8l3 1v2a1 1 0 0 1-1 1A9 9 0 0 1 2 3a1 1 0 0 1 1-1z"/></svg></span>
          <span>555-014-2203</span>
        </li>
        <li class="contact-item">
          <span class="contact-icon"><svg viewBox="0 0 14 14"><path d="M4 1h6v4H4zM2 6h10v6H2zm2 2v1h2V8zm4 0v1h2V8z"/></svg></span>
          <span>555-014-6681</span>
        </li>
        <li class="contact-item">
          <span class="contact-icon"><svg viewBox="0 0 14 14"><path d="M1 3h12v8H1zm1 1 5 4 5-4v-.2H2z"/></svg></span>
          <span>info@velmoranet.com</span>
        </li>
        <li class="contact-item">
          <span class="contact-icon"><svg viewBox="0 0 14 14"><path d="M7 1a6 6 0 1 0 0 12A6 6 0 0 0 7 1zm0 1.3c.8 0 1.6 1.8 1.8 3.9H5.2C5.4 4.1 6.2 2.3 7 2.3zM2.4 7.8h1.7c.1 1.5.5 2.8 1 3.6a4.8 4.8 0 0 1-2.7-3.6zm0-1.6A4.8 4.8 0 0 1 5.1 2.6c-.5.8-.9 2.1-1 3.6zm4.6 5.5c-.8 0-1.6-1.8-1.8-3.9h3.6c-.2 2.1-1 3.9-1.8 3.9zm1.9-.3c.5-.8.9-2.1 1-3.6h1.7a4.8 4.8 0 0 1-2.7 3.6zm1-5.2c-.1-1.5-.5-2.8-1-3.6a4.8 4.8 0 0 1 2.7 3.6z"/></svg></span>
          <span>www.velmoranet.com</span>
        </li>
      </ul>
    </div>
  </section>

</main>
</body>
</html>
```